SkyvornQ Business Cards and Stationary Design

Need a design for our business cards and stationary. I want to carry on the theme of the logo. I want the business cards to have a design on the back. I would like the business cards and the stationary to carry the same theme, design scheme, and branding

Target Market(s)

Airlines and Maintenance Facilities

Industry/Entity Type

Aviation

Contact Information for Business Card

Name
Position Title
Address: 4827 Trellis Hollow Road, Brenwick Falls, Alder County, 34951
Office Number
Mobile Number
Email
Website

Font styles to use
Serif
Sans Serif

Colors

Designer to choose colors to be used in the design.

```html
<!DOCTYPE html>
<html lang="en">
<head>
<meta charset="utf-8">
<title>SkyvornQ Business Card</title>
<link href="https://fonts.googleapis.com/css2?family=Open+Sans:wght@400;600;700&display=swap" rel="stylesheet">
<style>
:root{
  --bg:#2b2b2d;
  --card:#f7f7f8;
  --navy:#0f2f6e;
  --blue:#1f7fd1;
  --sky:#4cb0ee;
  --ink:#2f3440;
  --rule:#d9dce2;
}
*{margin:0;padding:0;box-sizing:border-box}
html,body{width:1200px;height:900px;overflow:hidden;background:var(--bg);font-family:"Open Sans",Arial,sans-serif}
.canvas{position:relative;width:1200px;height:900px}
.card{position:absolute;width:680px;height:390px;background:var(--card);border-radius:22px;overflow:hidden;box-shadow:0 14px 30px rgba(0,0,0,.45)}
.card-front{left:70px;top:50px}
.card-back{left:450px;top:470px}

.brand{display:flex;flex-direction:column;align-items:center;position:absolute}
.brand-mark{display:block}
.brand-name{font-weight:700;color:var(--navy);letter-spacing:.14em;text-transform:uppercase;line-height:1}
.card-front .brand{left:40px;top:78px;width:270px}
.card-front .brand-name{font-size:34px;margin-top:14px}

.divider{position:absolute;left:330px;top:30px;width:1px;height:215px;background:var(--rule)}

.contact{position:absolute;left:360px;top:52px;color:var(--ink)}
.person-name{font-size:22px;font-weight:700;color:var(--navy);text-transform:uppercase;letter-spacing:.02em}
.person-title{font-size:15px;color:#555;margin-bottom:14px}
.contact-list{list-style:none}
.contact-list li{display:flex;align-items:center;gap:10px;font-size:15px;line-height:25px}
.contact-list svg{width:13px;height:13px;fill:var(--navy);flex:none}

.band-edge{position:absolute;left:0;width:100%;height:3px;background:var(--sky)}
.band-edge.top{top:262px}
.band-edge.bottom{top:314px}
.band{position:absolute;left:0;top:268px;width:100%;height:43px;background:var(--navy);display:flex;align-items:center;justify-content:flex-end;padding-right:40px}
.address{color:#fff;font-size:16px;white-space:nowrap}

.card-back .brand{left:0;top:88px;width:100%}
.card-back .brand-name{font-size:44px;margin-top:16px}
.web-line{position:absolute;left:0;top:290px;width:100%;display:flex;align-items:center;justify-content:center;gap:14px}
.web-line .rule{width:70px;height:2px;background:var(--navy)}
.web-line span{font-size:17px;color:var(--navy);letter-spacing:.12em}
</style>
</head>
<body>
<main class="canvas">

  <section class="card card-front">
    <div class="brand">
      <svg class="brand-mark" width="70" height="70" viewBox="0 0 70 70"><circle cx="35" cy="35" r="30" fill="none" stroke="var(--blue)" stroke-width="5"/></svg>
      <div class="brand-name">SkyvornQ</div>
    </div>
    <div class="divider"></div>
    <div class="contact">
      <div class="person-name">Daniel Marsh</div>
      <div class="person-title">President</div>
      <ul class="contact-list">
        <li><svg viewBox="0 0 16 16"><path d="M3 1l3 3-1.5 2a9 9 0 0 0 5.5 5.5L12 10l3 3-2 2C7 15 1 9 1 3z"/></svg>001 555 0148</li>
        <li><svg viewBox="0 0 16 16"><path d="M4 0h8a1 1 0 0 1 1 1v14a1 1 0 0 1-1 1H4a1 1 0 0 1-1-1V1a1 1 0 0 1 1-1zm1 2v10h6V2z"/></svg>001 555 0149</li>
        <li><svg viewBox="0 0 16 16"><path d="M0 3h16v1L8 9 0 4zm0 3l8 5 8-5v7H0z"/></svg>info@skyvornq.com</li>
        <li><svg viewBox="0 0 16 16"><circle cx="8" cy="8" r="7" fill="none" stroke="var(--navy)" stroke-width="1.6"/><path d="M1 8h14M8 1c-3 3-3 11 0 14M8 1c3 3 3 11 0 14" fill="none" stroke="var(--navy)" stroke-width="1.2"/></svg>www.skyvornq.com</li>
      </ul>
    </div>
    <div class="band-edge top"></div>
    <div class="band"><span class="address">4827 Trellis Hollow Road, Brenwick Falls, Alder County, 34951</span></div>
    <div class="band-edge bottom"></div>
  </section>

  <section class="card card-back">
    <div class="brand">
      <svg class="brand-mark" width="90" height="90" viewBox="0 0 90 90"><circle cx="45" cy="45" r="39" fill="none" stroke="var(--blue)" stroke-width="6"/></svg>
      <div class="brand-name">SkyvornQ</div>
    </div>
    <div class="web-line">
      <i class="rule"></i><span>www.skyvornq.com</span><i class="rule"></i>
    </div>
  </section>

</main>
</body>
</html>
```